Harborline Renewal Business Card Design

Professional and clean design. The design colors should flow with the logo. Two-sided card with the website on the back which is:

www.HarborlineRenewal.example.

"Specializing in Water Damage Restoration"

On the front I need the name, email, phone, and logo.

Name: Darnell Quisby
Email: Darnell@HarborlineRenewal.example
Phone: 555-318-2046 for now

I only have the Preview and Thumbnail right now but should have the source files uploaded within a day or two.

Target Market(s)

Flood victims, home owners with water damage from busted pipes etc...

Industry/Entity Type

Business

Contact Information for Business Card

Name: Darnell Quisby

Font styles to use
Serif
Sans Serif

Requirements
Must have
• Business Card Details Info

```html
<!DOCTYPE html>
<html lang="en">
<head>
<meta charset="utf-8">
<title>Harborline Renewal – Business Card</title>
<link href="https://fonts.googleapis.com/css2?family=Cinzel:wght@400;500&family=Source+Sans+3:wght@400&display=swap" rel="stylesheet">
<style>
  :root {
    --brand-blue: #2e98d6;
    --brand-sky: #5ac2ee;
    --card-white: #ffffff;
    --ink: #2a2a2a;
    --stage: #eeebe5;
    --card-edge: #3a3a3a;
  }
  * { box-sizing: border-box; margin: 0; padding: 0; }
  html, body {
    width: 1200px; height: 980px; overflow: hidden;
    background: var(--stage);
  }
  .canvas { position: relative; width: 1200px; height: 980px; }

  .card {
    position: absolute; top: 40px;
    width: 506px; height: 879px;
  }

  /* Front */
  .card-front {
    left: 65px;
    background: var(--card-white);
    border: 1px solid var(--card-edge);
  }
  .brand-mark {
    position: absolute; left: 50%; top: 69px;
    width: 118px; height: 118px; margin-left: -59px;
    border-radius: 50%;
    background: var(--brand-blue);
  }
  .brand-name {
    position: absolute; left: 0; right: 0; top: 212px;
    text-align: center;
    font-family: "Cinzel", serif; font-weight: 500;
    color: var(--brand-blue);
  }
  .brand-name .primary {
    display: block; font-size: 58px; line-height: 1; letter-spacing: 1px;
  }
  .brand-name .secondary {
    display: block; font-size: 25px; line-height: 1; letter-spacing: 5px;
    margin-top: 8px;
  }
  .tagline {
    position: absolute; left: 0; right: 0; top: 355px;
    text-align: center;
    font-family: "Cinzel", serif; font-weight: 500;
    font-size: 24px; line-height: 30px; letter-spacing: 0.5px;
    color: var(--brand-blue);
  }

  .name-band-rule {
    position: absolute; left: 0; right: 0; height: 5px;
    background: var(--brand-sky);
  }
  .name-band-rule.upper { top: 483px; }
  .name-band-rule.lower { top: 599px; }
  .name-band {
    position: absolute; left: 0; right: 0; top: 492px; height: 101px;
    background: var(--brand-blue);
    color: var(--card-white);
    text-align: center;
    font-family: "Cinzel", serif; font-weight: 400;
    padding-top: 18px;
  }
  .name-band .person-name { display: block; font-size: 31px; line-height: 36px; letter-spacing: 0.5px; }
  .name-band .person-title { display: block; font-size: 26px; line-height: 30px; letter-spacing: 1px; }

  .contact-list {
    position: absolute; left: 0; right: 0; top: 682px;
    list-style: none;
    font-family: "Source Sans 3", sans-serif; font-size: 22px;
    color: var(--ink);
  }
  .contact-list li {
    display: flex; justify-content: center; align-items: center;
    gap: 9px; height: 45px;
  }
  .contact-icon { width: 18px; height: 18px; flex: none; }

  /* Back */
  .card-back {
    left: 628px;
    background: var(--brand-blue);
  }
  .back-mark {
    position: absolute; left: 103px; top: 238px;
    width: 295px; height: 295px; border-radius: 50%;
    background: var(--card-white);
  }
  .back-url {
    position: absolute; left: 0; right: 0; top: 579px;
    text-align: center;
    font-family: "Source Sans 3", sans-serif; font-size: 25px;
    letter-spacing: 1px;
    color: var(--card-white);
  }
</style>
</head>
<body>
<main class="canvas">

  <section class="card card-front" aria-label="Business card front">
    <div class="brand-mark" aria-hidden="true"></div>
    <h1 class="brand-name">
      <span class="primary">HARBORLINE</span>
      <span class="secondary">RENEWAL</span>
    </h1>
    <p class="tagline">Specializing in<br>Water Damage Restoration</p>

    <div class="name-band-rule upper"></div>
    <div class="name-band">
      <span class="person-name">Darnell Quisby</span>
      <span class="person-title">Title</span>
    </div>
    <div class="name-band-rule lower"></div>

    <ul class="contact-list">
      <li>
        <svg class="contact-icon" viewBox="0 0 20 20" aria-hidden="true">
          <circle cx="10" cy="10" r="9" fill="none" stroke="#2e98d6" stroke-width="1.6"/>
          <path d="M7 5.5c-1 1-1.2 3 .6 5.6s3.8 3.7 5 3.2l1-1.2-2-1.6-1 .8c-.8-.4-2-1.8-2.3-2.8l.8-1-1.3-2.2z" fill="#2e98d6"/>
        </svg>
        <span>555-318-2046</span>
      </li>
      <li>
        <svg class="contact-icon" viewBox="0 0 20 20" aria-hidden="true">
          <rect x="2" y="6" width="16" height="11" rx="1" fill="#2e98d6"/>
          <path d="M2 6.5l8 5.5 8-5.5" fill="none" stroke="#fff" stroke-width="1.4"/>
          <path d="M2 6l8-4 8 4" fill="none" stroke="#2e98d6" stroke-width="1.4"/>
        </svg>
        <span>Darnell@HarborlineRenewal.example</span>
      </li>
      <li>
        <svg class="contact-icon" viewBox="0 0 20 20" aria-hidden="true">
          <g fill="none" stroke="#2e98d6" stroke-width="1.3">
            <circle cx="10" cy="10" r="8"/>
            <ellipse cx="10" cy="10" rx="3.6" ry="8"/>
            <path d="M2 10h16M3.3 6h13.4M3.3 14h13.4"/>
          </g>
        </svg>
        <span>www.HarborlineRenewal.example</span>
      </li>
    </ul>
  </section>

  <section class="card card-back" aria-label="Business card back">
    <div class="back-mark" aria-hidden="true"></div>
    <p class="back-url">www.HarborlineRenewal.example</p>
  </section>

</main>
</body>
</html>
```